Flat Belly Design Graphics for Social

I want to create 9 social media graphics (new Instagram size 4:5 (1080 x 1350 pixels) focusing on our Flat Belly Graphics, using the pics attached. Use the attached pics, NO RANDOM STOCK PHOTOGRAPHY. For the color scheme of the graphics, the color palette is attached. YOU MUST POST ALL 9 GRAPHICS IN ONE ENTRY.
Using the 3 titles below, create one set of graphics. 1) with all text, then for the others, use the pictures as detailed below in IMPORTANT:
1. Ten-Week Bright Morning Reboot
2. The Quick Garden Kitchen Menu Guide
3. Studio Habits for Lasting Energy Past Midlife - Zero Gym Needed
IMPORTANT:
Only use RK Pic 1 and RK Pic 2 with the title, Ten-Week Bright Morning Reboot
Only use meal plan1 and meal plan2 pics with the title, Quick Garden Kitchen Menu Guide
Only use studio habits 1 and studio habits 2 pics with the title, Studio Habits for Lasting Energy Past Midlife - Zero Gym Needed
women over 40

```html
<!DOCTYPE html>
<html lang="en">
<head>
<meta charset="utf-8">
<title>Ten-Week Bright Morning Reboot – Social Set</title>
<link rel="stylesheet" href="https://fonts.googleapis.com/css2?family=Montserrat:wght@300;400;600;700;800;900&display=swap">
<style>
:root{
  --bg:#f9e9ec;
  --card:#f4c3cf;
  --card-soft:#f8d6de;
  --card-pale:#fbe6eb;
  --panel:#ee9fb4;
  --teal:#214a44;
  --pink:#e47f9b;
  --white:#ffffff;
  --frame:#efb3c2;
  --photo-warm-a:#f6d2da;
  --photo-warm-b:#7a5343;
  --photo-food-a:#6b4a33;
  --photo-food-b:#c44b45;
  --photo-sky-a:#7ccbdc;
  --photo-sky-b:#b7e3ea;
}
*{box-sizing:border-box;margin:0;padding:0}
html,body{width:1200px;height:720px;overflow:hidden;background:var(--bg);font-family:"Montserrat",sans-serif}
.grid{position:absolute;left:322px;top:16px;display:grid;grid-template-columns:repeat(3,177px);grid-template-rows:repeat(3,221px);gap:12px}
.card{position:relative;overflow:hidden;border:2px solid var(--frame);border-radius:9px;background:linear-gradient(160deg,var(--card-soft),var(--card))}
.card.pale{background:linear-gradient(170deg,var(--card-pale),var(--card-soft))}
.swoosh{position:absolute;inset:0;width:100%;height:100%}
.pill{position:absolute;left:50%;transform:translateX(-50%);top:10px;white-space:nowrap;background:var(--teal);color:var(--white);border-radius:10px;padding:2px 7px;font-size:6.6px;font-weight:400;letter-spacing:.1px}
.pill.big{font-size:11px;padding:2px 8px;top:9px}
.footer{position:absolute;left:7px;right:7px;bottom:0;height:13px;background:var(--teal);border-radius:6px 6px 0 0;color:var(--white);font-size:4.6px;display:flex;align-items:center;justify-content:center;gap:4px}
.footer .dot{width:5px;height:5px;border-radius:50%;background:var(--white)}
.footer b{font-weight:700}
.badge{position:absolute;width:48px;height:48px;border-radius:50%;background:var(--white);opacity:.85}
.photo{position:absolute}
.t{position:absolute;color:var(--teal);line-height:1}
.light{font-weight:300}
.heavy{font-weight:800}
.center{left:0;right:0;text-align:center}
</style>
</head>
<body>
<main class="grid">

  <section class="card">
    <div class="photo" role="img" aria-label="Smiling woman in a white cropped sweater pointing to her toned midriff" style="right:0;top:18px;width:102px;height:186px;background:linear-gradient(180deg,var(--photo-warm-a),#e9c2b2 45%,var(--photo-warm-b) 100%);border-radius:40px 0 0 0;opacity:.9"></div>
    <div class="pill big">FLAT TUMMY AFTER 40?</div>
    <div class="t heavy" style="left:8px;top:30px;font-size:22px">YES!</div>
    <div class="t light" style="left:8px;top:52px;font-size:14px">IN JUST</div>
    <div class="t heavy" style="left:8px;top:67px;font-size:13px">TEN WEEKS!</div>
    <div class="t light" style="left:8px;top:90px;font-size:8px;line-height:1.35">No extreme<br>workouts.<br>No starving.</div>
    <div class="badge" style="left:6px;top:152px"></div>
    <div class="footer"><span class="dot"></span>Ten-Week Bright Morning Reboot | <b>Learn More ›</b></div>
  </section>

  <section class="card pale">
    <div style="position:absolute;left:7px;right:7px;top:7px;bottom:18px;border-radius:6px;background:linear-gradient(160deg,#f5c9d4,var(--panel))"></div>
    <div class="pill">FLAT TUMMY AFTER 40?</div>
    <div class="badge" style="left:63px;top:34px;width:50px;height:50px"></div>
    <div class="t light center" style="top:102px;font-size:8px;color:var(--white);line-height:1.2">OVER 40 AND<br>STUBBORN BELLY FAT?</div>
    <div class="t center" style="top:126px;font-size:10px;font-weight:700;line-height:1.25">This Ten-Week<br>Bright Morning<br>Reboot is<br><span class="heavy">MADE FOR YOU!</span></div>
    <div class="footer"><span class="dot"></span>Ten-Week Bright Morning Reboot | <b>Learn More ›</b></div>
  </section>

  <section class="card pale">
    <svg class="swoosh" viewBox="0 0 177 221" aria-hidden="true"><path d="M0 70 C50 40 120 110 177 60 L177 0 L0 0Z" fill="#f6cad5" opacity=".6"/></svg>
    <div class="pill" style="left:60px">FLAT TUMMY AFTER 40?</div>
    <div class="t light" style="left:13px;top:28px;font-size:14px;line-height:.95">You don’t<br>need hours<br>in the gym.</div>
    <div class="badge" style="right:6px;top:10px;width:46px;height:46px"></div>
    <div class="t heavy center" style="top:88px;font-size:13px;line-height:1.1">YOU NEED<br>THE RIGHT</div>
    <div class="t center" style="top:118px;font-size:25px;font-weight:900;line-height:1">TEN-WEEK<br>RESET</div>
    <div class="footer"><span class="dot"></span>Ten-Week Bright Morning Reboot | <b>Learn More ›</b></div>
  </section>

  <section class="card pale">
    <div class="photo" role="img" aria-label="Wooden table with fresh vegetables, fruit bowls, grains and a printed meal plan sheet" style="left:0;right:0;bottom:0;height:118px;background:linear-gradient(160deg,var(--photo-food-b) 0%,#8aa25a 35%,var(--photo-food-a) 70%,#3e2c1f 100%);clip-path:polygon(0 30%,60% 10%,100% 0,100% 100%,0 100%)"></div>
    <div class="pill">The Quick Garden Kitchen Menu Guide</div>
    <div class="t" style="left:11px;top:26px;font-size:18px;font-weight:800;color:var(--pink);line-height:1">Only<br>15 minutes<br>to Cook.</div>
    <div class="t" style="left:11px;top:84px;font-size:7.4px;line-height:1.25;font-weight:400">Results that<br>last way longer</div>
    <div class="badge" style="right:10px;top:58px"></div>
    <div class="footer"><span class="dot"></span>Ten-Week Bright Morning Reboot | <b>Learn More ›</b></div>
  </section>

  <section class="card">
    <svg class="swoosh" viewBox="0 0 177 221" aria-hidden="true"><path d="M0 100 L177 70 L177 0 L0 0Z" fill="#f7d3dc" opacity=".55"/><path d="M8 118 L170 88 L170 176 L8 206Z" fill="#f0a5b9"/></svg>
    <div class="pill">The Quick Garden Kitchen Menu Guide</div>
    <div class="t light" style="left:30px;top:42px;font-size:16px;color:var(--white);transform:rotate(-12deg);transform-origin:left top;line-height:1.15">Busy life.<br>Real food.</div>
    <div class="badge" style="right:10px;top:26px;width:42px;height:42px"></div>
    <div class="t heavy center" style="top:110px;font-size:15px;line-height:1.05;transform:rotate(-12deg)">A FLAT BELLY<br>MEAL PLAN<br>THAT ACTUALLY<br>FITS YOUR DAY</div>
    <div class="footer"><span class="dot"></span>Ten-Week Bright Morning Reboot | <b>Learn More ›</b></div>
  </section>

  <section class="card">
    <svg class="swoosh" viewBox="0 0 177 221" aria-hidden="true"><path d="M0 120 C60 90 110 150 177 110 L177 221 L0 221Z" fill="#f7d2db" opacity=".6"/><circle cx="147" cy="146" r="24" fill="#ee97ae" opacity=".55"/><path d="M136 146 l8 8 l14 -16" stroke="#fbdce3" stroke-width="5" fill="none" stroke-linecap="round" stroke-linejoin="round"/></svg>
    <div class="pill">The Quick Garden Kitchen Menu Guide</div>
    <div class="t light center" style="top:30px;font-size:10.5px;color:var(--white);line-height:1.3">No counting calories.<br>No complicated recipes.</div>
    <div class="badge" style="left:16px;top:62px;width:42px;height:42px"></div>
    <div class="t heavy" style="left:66px;top:90px;font-size:16.5px">JUST</div>
    <div class="t heavy center" style="top:109px;font-size:16.5px;line-height:1.15">15 MINUTES<br>TO A<br>FLATTER BELLY</div>
    <div class="footer"><span class="dot"></span>Ten-Week Bright Morning Reboot | <b>Learn More ›</b></div>
  </section>

  <section class="card pale">
    <div class="photo" role="img" aria-label="Two women sharing a whispered secret against a sky-blue backdrop" style="left:0;right:0;top:0;height:124px;background:linear-gradient(135deg,var(--photo-sky-a),var(--photo-sky-b));border-radius:0 0 8px 8px"></div>
    <div class="badge" style="right:8px;top:58px"></div>
    <div class="pill" style="top:130px;font-size:6.2px">Studio Habits for Lasting Energy Past Midlife</div>
    <div class="t light center" style="top:144px;font-size:8.6px;color:var(--pink);line-height:1.3">Celebrities over 40<br>aren’t doing magic…</div>
    <div class="t center" style="top:169px;font-size:12.5px;font-weight:400">They’re using these</div>
    <div class="t heavy center" style="top:184px;font-size:12.5px">TINY-WAIST SECRETS</div>
    <div class="footer"><span class="dot"></span>Ten-Week Bright Morning Reboot | <b>Learn More ›</b></div>
  </section>

  <section class="card">
    <svg class="swoosh" viewBox="0 0 177 221" aria-hidden="true"><path d="M0 60 C40 10 90 10 177 40 L177 0 L0 0Z" fill="#f8d6de" opacity=".7"/><path d="M0 180 L177 130 L177 221 L0 221Z" fill="#fbe3e8"/></svg>
    <div class="pill" style="font-size:6.2px">Studio Habits for Lasting Energy Past Midlife</div>
    <div class="badge" style="right:12px;top:58px;width:42px;height:42px"></div>
    <div class="t light" style="left:40px;top:42px;font-size:12px;color:var(--white);transform:rotate(28deg);transform-origin:left top;line-height:1">TINY WAIST<br>AFTER 40</div>
    <div class="t heavy" style="left:22px;top:70px;font-size:14px;transform:rotate(28deg);transform-origin:left top;line-height:1.05;white-space:nowrap">NO SURGERY.<br>NO CRAZY DIETS.<br><span style="font-weight:700">Just smart habits</span></div>
    <div class="footer"><span class="dot"></span>Ten-Week Bright Morning Reboot | <b>Learn More ›</b></div>
  </section>

  <section class="card pale">
    <div class="pill" style="font-size:6.2px">Studio Habits for Lasting Energy Past Midlife</div>
    <div class="t light" style="left:10px;top:34px;font-size:19px;color:var(--pink);line-height:1.05">EVER WONDER<br>HOW</div>
    <div class="t heavy" style="left:10px;top:77px;font-size:19px;color:var(--pink);line-height:1.1">CELEBRITIES<br>STAY SLIM<br>AFTER 40?</div>
    <div class="badge" style="right:8px;top:124px;width:44px;height:44px"></div>
    <div class="t light center" style="top:176px;font-size:10px;color:var(--pink);line-height:1.2">Here’s the truth<br>they don’t talk about</div>
    <div class="footer"><span class="dot"></span>Ten-Week Bright Morning Reboot | <b>Learn More ›</b></div>
  </section>

</main>
</body>
</html>
```